Bork Ventures, Inc. Website redesign

Revamp the website, it is old and outdated. www.borkventuresinc.example

Target Market(s)

Information Technology Consulting and Staffing

Coding

Coded - Design and coding required

Number of Pages Required

5+ page

Colors

Designer to choose colors to be used in the design.

Requirements
Must have
• Outlined text boxes just like from the Tolvane.example site. A clean look

```html
<!DOCTYPE html>
<html lang="en">
<head>
<meta charset="utf-8">
<title>Bork Ventures, Inc.</title>
<link rel="stylesheet" href="https://fonts.googleapis.com/css2?family=Roboto:wght@300;400;500;700;900&display=swap">
<style>
:root{
  --red:#9e1b32;
  --red-dark:#7d1226;
  --ink:#111;
  --text:#555;
  --grey-band:#e6e6e6;
  --pink-band:#f8dfe5;
  --white:#fff;
  --black:#000;
}
*{box-sizing:border-box;margin:0;padding:0}
html,body{width:1200px;height:3511px;overflow:hidden}
body{position:relative;background:var(--white);font-family:'Roboto',sans-serif;color:var(--text)}
.abs{position:absolute}
svg.abs{display:block}
.btn{position:absolute;height:38px;background:var(--red);color:var(--white);font-weight:700;font-size:17px;display:flex;align-items:center;justify-content:center;gap:8px;letter-spacing:-.2px}
.btn .arrow{width:15px;height:15px;border-radius:50%;background:var(--white);color:var(--red);font-size:10px;display:flex;align-items:center;justify-content:center;font-weight:900}
.section-title{position:absolute;left:0;width:1200px;text-align:center;font-weight:900;font-size:40px;color:var(--ink);letter-spacing:-.5px}
.dots{position:absolute;left:0;width:1200px;display:flex;justify-content:center;gap:13px}
.dots span{width:16px;height:16px;border-radius:50%;background:var(--red)}
.dots span.active{background:transparent;border:2px solid var(--red)}

/* header */
.site-header{position:absolute;left:0;top:0;width:1200px;height:97px;background:var(--white)}
.brand{position:absolute;left:110px;top:26px;display:flex;align-items:center;gap:12px;font-weight:900;font-size:30px;color:#222;letter-spacing:-.5px}
.brand i{width:26px;height:26px;background:var(--red);display:block}
.main-nav{position:absolute;left:465px;top:37px;display:flex;gap:21px;font-weight:500;font-size:16px;color:#111}
.main-nav a{color:inherit;text-decoration:none;position:relative}
.main-nav a.current{color:var(--red)}
.main-nav a.current::after{content:"";position:absolute;left:0;right:0;top:30px;height:4px;background:var(--red)}

/* hero */
.hero-photo{position:absolute;left:0;top:97px;width:1200px;height:564px;background:linear-gradient(100deg,#1c3d63 0%,#2b6b9c 35%,#163050 65%,#0e1e33 100%)}
.hero-title{position:absolute;left:0;top:222px;width:1200px;text-align:center;color:var(--white);font-weight:900;font-size:56px}
.hero-sub{position:absolute;left:0;top:298px;width:1200px;text-align:center;color:var(--white);font-size:18px;line-height:27px}

/* about */
.about-title{left:117px;top:740px;font-weight:900;font-size:40px;color:var(--ink)}
.about-text{left:110px;top:809px;width:415px;font-size:15px;line-height:25.5px;color:#555;font-weight:300}
.about-text p+p{margin-top:26px}
.about-frame{left:562px;top:753px;width:520px;height:323px;border:4px solid var(--red)}
.about-frame::before,.about-frame::after{content:"";position:absolute;left:150px;width:212px;height:8px;background:var(--white)}
.about-frame::before{top:-6px}.about-frame::after{bottom:-6px}
.about-gap-l,.about-gap-r{position:absolute;top:140px;width:8px;height:60px;background:var(--white)}
.about-gap-l{left:-6px}.about-gap-r{right:-6px}
.about-photo{left:570px;top:762px;width:505px;height:305px;background:linear-gradient(120deg,#2d3a4a,#6b7d8c 45%,#c7ccd2 70%,#3e4a2a);border:2px solid var(--white)}

/* services */
.service-card{position:absolute;top:1337px;width:317px;height:433px;background:var(--white);box-shadow:0 0 6px rgba(0,0,0,.18);text-align:center}
.service-card .lead{position:absolute;top:18px;left:30px;right:30px;font-size:15px;line-height:25px;color:#222}
.service-card .photo{position:absolute;left:3px;right:3px;top:86px;height:174px}
.service-card .icon{position:absolute;left:50%;top:232px;margin-left:-29px;width:58px;height:58px;border-radius:50%;background:var(--white);box-shadow:0 0 4px rgba(0,0,0,.2);display:flex;align-items:center;justify-content:center}
.service-card h3{position:absolute;top:300px;left:0;right:0;font-weight:500;font-size:19px;color:#111}
.service-card .desc{position:absolute;top:334px;left:20px;right:20px;font-size:15px;line-height:26px;color:#666;font-weight:300}
.service-card .btn{left:78px;top:411px;width:161px}

/* strategy */
.strategy-text{position:absolute;left:135px;top:2039px;width:930px;text-align:center;font-size:16.5px;line-height:26px;color:#555}

/* news */
.news-card{position:absolute;width:477px;height:136px;background:var(--white);box-shadow:0 0 6px rgba(0,0,0,.2)}
.news-date{position:absolute;left:4px;top:4px;width:110px;height:128px;background:var(--black);color:var(--white);text-align:center}
.news-card.featured .news-date{background:var(--red)}
.news-date svg{margin-top:14px}
.news-date .day{font-size:26px;font-weight:700;margin-top:6px}
.news-date .month{font-size:15px;margin-top:2px}
.news-card h4{position:absolute;left:158px;top:20px;font-weight:500;font-size:18px;color:#111}
.news-card p{position:absolute;left:160px;top:58px;width:300px;font-size:14.5px;line-height:26px;color:#666;font-weight:300}

/* footer */
.site-footer{position:absolute;left:0;top:2960px;width:1200px;height:551px}
.newsletter-label{left:164px;top:3127px;color:var(--white);font-weight:500;font-size:25px}
.newsletter-form{left:547px;top:3120px;width:488px;height:46px;background:var(--white);border:2px solid var(--red);display:flex}
.newsletter-form .field{flex:1;display:flex;align-items:center;gap:14px;padding-left:20px;font-size:16px;color:#777}
.newsletter-form .submit{width:140px;background:var(--red);color:var(--white);font-weight:700;font-size:16px;display:flex;align-items:center;justify-content:center}
.footer-rule{left:110px;top:3196px;width:978px;height:1px;background:#555}
.footer-col{position:absolute;top:3246px;color:var(--white)}
.footer-col h5{font-weight:700;font-size:18px;text-decoration:underline;text-underline-offset:4px;margin-bottom:14px}
.footer-col li{list-style:none;font-size:17px;height:35.3px;display:flex;align-items:flex-start;gap:14px;padding-left:0}
.footer-col li::before{content:"»";font-size:17px;line-height:20px}
.copyright{left:0;top:3460px;width:1200px;height:51px;background:#111;color:var(--white);font-size:17px;display:flex;align-items:center;justify-content:center}
</style>
</head>
<body>

<header class="site-header">
  <div class="brand"><i></i>Bork Ventures</div>
  <nav class="main-nav">
    <a class="current">HOME</a><a>ABOUT US</a><a>SERVICES</a><a>STRATEGY</a><a>IT NEWS</a><a>CONTACT US</a>
  </nav>
</header>

<section>
  <div class="hero-photo" role="img" aria-label="Network diagram with data centre server racks in blue light"></div>
  <svg class="abs" style="left:0;top:520px" width="1200" height="145" viewBox="0 0 1200 145">
    <polygon points="0,0 600,110 1200,0 1200,145 0,145" fill="#fff"/>
    <polygon points="0,2 600,112 1130,20 1200,10 1200,16 600,142 0,30" fill="#9e1b32"/>
    <polygon points="0,30 600,142 1200,16 1200,145 0,145" fill="#fff"/>
  </svg>
  <h1 class="hero-title">BORK VENTURES</h1>
  <p class="hero-sub">We believe the technology supporting your business operations. should align with your company.<br>Every project begins with a thorough analysis of your current technology.</p>
  <div class="btn" style="left:519px;top:373px;width:161px">READ MORE <span class="arrow">➜</span></div>
  <div class="dots" style="top:456px"><span></span><span style="background:#fff"></span><span></span><span></span></div>
</section>

<section>
  <h2 class="abs about-title">ABOUT US</h2>
  <div class="abs about-text">
    <p>Bork Ventures, Inc. is an 8(a) innovative and rapidly growing full-service IT consulting firm. We provide our clients with cutting-edge technologies and the know-how to apply them to their individual business models.</p>
    <p>For over 20 + years, we have been providing reliable IT solutions to businesses in the Washington, DC Metro area and beyond. Our comprehensive services.</p>
  </div>
  <div class="btn" style="left:110px;top:1035px;width:162px">READ MORE <span class="arrow">➜</span></div>
  <div class="abs about-frame"><span class="about-gap-l"></span><span class="about-gap-r"></span></div>
  <div class="abs about-photo" role="img" aria-label="Laptop in front of a network patch panel with cables"></div>
</section>

<section>
  <svg class="abs" style="left:0;top:1168px" width="1200" height="354" viewBox="0 0 1200 354">
    <polygon points="0,102 600,0 1200,102 1200,354 0,354" fill="#e6e6e6"/>
  </svg>
  <h2 class="section-title" style="top:1242px">OUR SERVICES</h2>

  <article class="service-card" style="left:110px">
    <p class="lead">Excepteur sint occaecat cupidatat non proident</p>
    <div class="photo" role="img" aria-label="Hands typing on a laptop keyboard with audit graphics" style="background:linear-gradient(120deg,#e8e8e8,#7a7a7a 50%,#2a2a2a)"></div>
    <div class="icon"><svg width="26" height="26" viewBox="0 0 26 26" fill="none" stroke="#9e1b32" stroke-width="2"><rect x="3" y="3" width="20" height="14"/><path d="M9 23h8M13 17v6"/><circle cx="13" cy="10" r="3"/></svg></div>
    <h3>HARDWARE / SOFTWARE SALES</h3>
    <p class="desc">We have access to multiple distributor partners throughout North America.</p>
    <div class="btn">READ MORE <span class="arrow">➜</span></div>
  </article>

  <article class="service-card" style="left:441px">
    <p class="lead">sed do eiusmod tempor incididunt ut labore et dolore</p>
    <div class="photo" role="img" aria-label="Two technicians reviewing a laptop in a server room" style="background:linear-gradient(90deg,#0f3a66,#3a7fc0 50%,#0d2f55)"></div>
    <div class="icon"><svg width="26" height="26" viewBox="0 0 26 26" fill="none" stroke="#9e1b32" stroke-width="2"><circle cx="13" cy="8" r="5"/><path d="M3 24c1-6 5-9 10-9s9 3 10 9z"/></svg></div>
    <h3>PROFESSIONAL SERVICES</h3>
    <p class="desc">Our team provides experienced leadership and guidance, utilizing.</p>
    <div class="btn">READ MORE <span class="arrow">➜</span></div>
  </article>

  <article class="service-card" style="left:771px">
    <p class="lead">Duis aute irure dolor in reprehenderit</p>
    <div class="photo" role="img" aria-label="Hand touching a digital compliance dial" style="background:linear-gradient(90deg,#1a6fd0,#0b3d8a 50%,#05142e)"></div>
    <div class="icon"><svg width="26" height="26" viewBox="0 0 26 26" fill="none" stroke="#9e1b32" stroke-width="2"><rect x="4" y="3" width="16" height="20"/><path d="M8 9h8M8 13h8M8 17h5"/></svg></div>
    <h3>TECHNOLOGY ASSESSMENT</h3>
    <p class="desc">Experience has shown companies that perform objective, third-party.</p>
    <div class="btn">READ MORE <span class="arrow">➜</span></div>
  </article>

  <div class="dots" style="top:1813px"><span></span><span class="active"></span><span></span><span></span></div>
</section>

<section>
  <svg class="abs" style="left:0;top:1883px" width="1200" height="507" viewBox="0 0 1200 507">
    <polygon points="0,85 600,0 1200,85 1200,420 600,507 0,420" fill="#f8dfe5"/>
  </svg>
  <div class="abs" role="img" aria-label="Faint photo of a support agent wearing a headset" style="left:560px;top:1883px;width:300px;height:507px;background:linear-gradient(180deg,rgba(230,190,200,.25),rgba(230,190,200,.1))"></div>
  <h2 class="section-title" style="top:1968px">OUR STRATEGY</h2>
  <p class="strategy-text">Civilian and Federal agencies are facing increased demands driven by the changing economic environment and shifts in the way products and services are sold and delivered. These factors have created an imperative to leverage new and innovative technology solution architectures like cloud computing to help reduce cost and deliver profit-driving IT capabilities faster than ever before. Savvy businesses understand that technology investments cannot be made solely to enable internal and external operations; technology.</p>
  <div class="btn" style="left:519px;top:2203px;width:161px">READ MORE <span class="arrow">➜</span></div>
  <div class="dots" style="top:2280px"><span></span><span class="active"></span><span></span><span></span></div>
</section>

<section>
  <h2 class="section-title" style="top:2463px">LATEST NEWS</h2>
  <article class="news-card" style="left:110px;top:2550px">
    <div class="news-date"><svg width="24" height="24" viewBox="0 0 24 24" fill="#fff"><rect x="2" y="4" width="20" height="18" rx="1"/><rect x="4" y="9" width="16" height="11" fill="#000"/><rect x="6" y="1" width="3" height="5"/><rect x="15" y="1" width="3" height="5"/></svg><div class="day">28</div><div class="month">August</div></div>
    <h4>LOREM IPSUM DOLOR SIT AMET</h4>
    <p>Sed ut perspiciatis unde omnis iste natus error sit voluptatem accusantium.</p>
  </article>
  <article class="news-card featured" style="left:611px;top:2550px">
    <div class="news-date"><svg width="24" height="24" viewBox="0 0 24 24" fill="#fff"><rect x="2" y="4" width="20" height="18" rx="1"/><rect x="4" y="9" width="16" height="11" fill="#9e1b32"/><rect x="6" y="1" width="3" height="5"/><rect x="15" y="1" width="3" height="5"/></svg><div class="day">29</div><div class="month">August</div></div>
    <h4>LOREM IPSUM DOLOR SIT AMET</h4>
    <p>Sed ut perspiciatis unde omnis iste natus error sit voluptatem accusantium.</p>
  </article>
  <article class="news-card" style="left:110px;top:2722px">
    <div class="news-date"><svg width="24" height="24" viewBox="0 0 24 24" fill="#fff"><rect x="2" y="4" width="20" height="18" rx="1"/><rect x="4" y="9" width="16" height="11" fill="#000"/><rect x="6" y="1" width="3" height="5"/><rect x="15" y="1" width="3" height="5"/></svg><div class="day">30</div><div class="month">August</div></div>
    <h4>LOREM IPSUM DOLOR SIT AMET</h4>
    <p>Sed ut perspiciatis unde omnis iste natus error sit voluptatem accusantium.</p>
  </article>
  <article class="news-card" style="left:611px;top:2722px">
    <div class="news-date"><svg width="24" height="24" viewBox="0 0 24 24" fill="#fff"><rect x="2" y="4" width="20" height="18" rx="1"/><rect x="4" y="9" width="16" height="11" fill="#000"/><rect x="6" y="1" width="3" height="5"/><rect x="15" y="1" width="3" height="5"/></svg><div class="day">31</div><div class="month">August</div></div>
    <h4>LOREM IPSUM DOLOR SIT AMET</h4>
    <p>Sed ut perspiciatis unde omnis iste natus error sit voluptatem accusantium.</p>
  </article>
</section>

<footer class="site-footer">
  <svg class="abs" style="left:0;top:0" width="1200" height="551" viewBox="0 0 1200 551">
    <polygon points="0,148 600,10 1200,148 1200,551 0,551" fill="#9e1b32"/>
    <polygon points="0,155 600,40 1200,155 1200,551 0,551" fill="#000"/>
    <polygon points="60,150 600,10 1200,140 1200,148 600,14 0,150" fill="#9e1b32"/>
  </svg>
</footer>
<div class="abs newsletter-label">JOIN OUR NEWSLETTER</div>
<div class="abs newsletter-form">
  <div class="field"><svg width="18" height="14" viewBox="0 0 18 14" fill="none" stroke="#9e1b32" stroke-width="1.6"><rect x="1" y="1" width="16" height="12"/><path d="M1 1l8 7 8-7"/></svg>Email</div>
  <div class="submit">SUBSCRIBE</div>
</div>
<div class="abs footer-rule"></div>
<nav class="footer-col" style="left:123px"><h5>QUICK LINKS</h5><ul><li>Home</li><li>About Us</li><li>Services</li><li>Stradegy</li><li>News</li></ul></nav>
<nav class="footer-col" style="left:372px"><h5>OTHER LINKS</h5><ul><li>FAQ</li><li>Blog</li><li>Reviews</li><li>Help</li><li>Terms &amp; Conditions</li></ul></nav>
<nav class="footer-col" style="left:625px"><h5>OUR SERVICES</h5><ul><li>Software Sales</li><li>Professional Services</li><li>Technology Assessment</li><li>Technology Consulting</li></ul></nav>
<nav class="footer-col" style="left:962px"><h5>STRATEGIES</h5><ul><li>Recommend</li><li>Implement</li><li>Monitor</li><li>Manage</li><li>Assess</li></ul></nav>
<div class="abs copyright">© 2019 Bork Ventures. All Rights Reserved</div>

</body>
</html>
```